Hvac and insulation company needs good looking business card design

We are hvac and insulation company and looking for a new business cards that look to today standards designs

Target Market(s)

homeowners

Industry/Entity Type

Hvac

Contact Information for Business Card

Name: Walter Brinoku
Home comfort consultant
address: 4827 Dunmore St #215 Oakland, CA 94619
office: 888-316-2790
cell: 510-742-3185
Lic.# 584261
Email: walter@corvane-hvac.com
Web: corvane-hvac.com

Requirements
Must have
• clean and sleek look
Nice to have
• simple with a clean look
Should not have
• to busy business card

```html
<!DOCTYPE html>
<html lang="en">
<head>
<meta charset="utf-8">
<title>Corvane Home Solutions — Business Card</title>
<link rel="stylesheet" href="https://fonts.googleapis.com/css2?family=Oswald:wght@500&family=Open+Sans:wght@400;600&display=swap">
<style>
  :root {
    --backdrop: #2a2a2a;
    --card: #1d1d1d;
    --orange: #ee8a12;
    --white: #f2f2f2;
    --silver: #b9b9b9;
  }
  * { margin: 0; padding: 0; box-sizing: border-box; }
  html, body { width: 1200px; height: 900px; overflow: hidden; }
  body {
    background: var(--backdrop);
    font-family: "Open Sans", sans-serif;
    display: flex;
    flex-direction: column;
    align-items: center;
    justify-content: center;
    gap: 44px;
  }
  .card {
    width: 600px;
    height: 343px;
    background: var(--card);
    position: relative;
    overflow: hidden;
    box-shadow: 0 10px 30px rgba(0,0,0,.45);
  }

  /* Back side */
  .card-back .brand {
    position: absolute;
    top: 118px; left: 0; right: 0;
    display: flex; align-items: center; justify-content: center; gap: 14px;
  }
  .brand-mark { width: 34px; height: 34px; background: var(--silver); flex: none; }
  .brand-name {
    font-weight: 600; font-size: 40px; line-height: 1;
    letter-spacing: 1px; color: var(--silver);
  }
  .card-back .web {
    position: absolute; bottom: 38px; left: 0; right: 0;
    display: flex; justify-content: center; align-items: center; gap: 10px;
    font-size: 15px; color: var(--white); letter-spacing: .5px;
  }
  .accent { color: var(--orange); }
  .icon { width: 16px; height: 16px; flex: none; }

  /* Front side */
  .card-front .brand {
    position: absolute; top: 108px; left: 38px;
    width: 262px;
    display: flex; align-items: center; gap: 12px;
  }
  .card-front .brand-mark { width: 30px; height: 30px; background: var(--orange); }
  .card-front .brand-name {
    color: var(--orange); font-size: 32px; line-height: 1.12; letter-spacing: .5px;
  }
  .divider {
    position: absolute; left: 322px; top: 78px;
    width: 2px; height: 172px; background: var(--white);
  }
  .contact { position: absolute; left: 346px; top: 74px; color: var(--white); }
  .person-name {
    font-family: "Oswald", sans-serif; font-weight: 500;
    font-size: 32px; line-height: 1; letter-spacing: .5px; text-transform: uppercase;
  }
  .person-role {
    font-weight: 600; font-size: 14px; color: var(--orange);
    margin-top: 4px; letter-spacing: .3px;
  }
  .license { font-size: 14px; margin-top: 12px; }
  .details { list-style: none; margin-top: 8px; }
  .details li {
    display: flex; align-items: center; gap: 12px;
    font-size: 14px; line-height: 22px;
  }
  .address {
    position: absolute; left: 78px; bottom: 36px;
    font-size: 15px; color: var(--white); letter-spacing: .6px;
  }
  .address .label { color: var(--orange); }
</style>
</head>
<body>

  <section class="card card-back">
    <div class="brand">
      <span class="brand-mark"></span>
      <span class="brand-name">corvane home solutions</span>
    </div>
    <p class="web">
      <svg class="icon" viewBox="0 0 16 16" fill="none" stroke="#ee8a12" stroke-width="1.2"><circle cx="8" cy="8" r="6.5"/><ellipse cx="8" cy="8" rx="3" ry="6.5"/><path d="M1.5 8h13M2.5 4.8h11M2.5 11.2h11"/></svg>
      <span>www.<span class="accent">corvane-hvac</span>.com</span>
    </p>
  </section>

  <section class="card card-front">
    <div class="brand">
      <span class="brand-mark"></span>
      <span class="brand-name">corvane home solutions</span>
    </div>

    <div class="divider"></div>

    <div class="contact">
      <h1 class="person-name">Walter Brinoku</h1>
      <p class="person-role">Home comfort consultant</p>
      <p class="license">Lic #584261</p>
      <ul class="details">
        <li>
          <svg class="icon" viewBox="0 0 16 16" fill="none" stroke="#ee8a12" stroke-width="1.4"><rect x="4" y="1.5" width="8" height="13" rx="1.2"/><path d="M7 12.5h2"/></svg>
          <span>888 316 2790</span>
        </li>
        <li>
          <svg class="icon" viewBox="0 0 16 16" fill="#ee8a12"><path d="M4.5 2 6.6 4.6 5.3 6.3c.8 1.7 2.1 3 3.8 3.8l1.6-1.3L13.3 11l-1.6 2.2C7 12.8 3 8.8 2.6 4z"/></svg>
          <span>510 742 3185</span>
        </li>
        <li>
          <svg class="icon" viewBox="0 0 16 16" fill="none" stroke="#ee8a12" stroke-width="1.4"><rect x="1.5" y="3.5" width="13" height="9" rx="1"/><path d="m1.8 4 6.2 5 6.2-5"/></svg>
          <span>walter@corvane-hvac.com</span>
        </li>
        <li>
          <svg class="icon" viewBox="0 0 16 16" fill="none" stroke="#ee8a12" stroke-width="1.2"><circle cx="8" cy="8" r="6.5"/><ellipse cx="8" cy="8" rx="3" ry="6.5"/><path d="M1.5 8h13M2.5 4.8h11M2.5 11.2h11"/></svg>
          <span>www.<span class="accent">corvane-hvac</span>.com</span>
        </li>
      </ul>
    </div>

    <p class="address"><span class="label">Address</span> - 4827 Dunmore St #215 Oakland, CA 94619</p>
  </section>

</body>
</html>
```